Bramblewood Joinery Website

My client Bramblewood Joinery is looking for a redesign for a Word Press Website. Their current site is at www.bramblewoodjoinery.example They are a custom cabinet company, but also create bathroom, living room, bar and entertainment and bedroom cabinets too. They would like a design that emulates the master craftsman work they do yet a contemporary style.

Their current site was designed using Flash elements.

Target Market(s)

Home owners and builders of high end homes

Industry/Entity Type

Entertainment

Font styles to use
Serif
Decorative

Requirements
Must have
• Must show their work and logo using a contemporary style.
Nice to have
• Sliders that showcase their projects.

```html
<!DOCTYPE html>
<html lang="en">
<head>
<meta charset="utf-8">
<title>Bramblewood Joinery</title>
<link href="https://fonts.googleapis.com/css2?family=Noto+Serif:ital,wght@0,400;1,400&family=Mulish:wght@400;500&family=Oswald:wght@500&family=Roboto+Condensed:wght@400&display=swap" rel="stylesheet">
<style>
:root{
  --white:#ffffff;
  --ink:#1b1b1b;
  --text:#4a4a4a;
  --muted:#7a7a7a;
  --green:#3cb44b;
  --lime:#8cc63f;
  --nav:#1a1a1a;
  --band:#3d3839;
  --foot:#1f1d1e;
  --dot:#d8d8d8;
}
*{margin:0;padding:0;box-sizing:border-box}
html,body{width:1200px;height:1074px;overflow:hidden;background:var(--white)}
body{position:relative;font-family:'Mulish',sans-serif;color:var(--ink)}
.topbar{position:absolute;left:0;top:0;width:1200px;height:87px;background:var(--white)}
.follow{position:absolute;right:122px;top:18px;display:flex;align-items:center;gap:10px;font-size:14px;color:var(--muted)}
.follow .icon{width:16px;height:16px;border-radius:50%;background:#333}
.utility{position:absolute;right:122px;top:51px;font-size:14px;font-weight:500;display:flex;gap:16px;color:var(--ink)}
.utility span.sep{color:#555}
.mainnav{position:absolute;left:0;top:87px;width:1200px;height:48px;background:var(--nav);border-bottom:4px solid var(--green);height:52px}
.mainnav ul{list-style:none;position:absolute;left:342px;top:12px;display:flex;gap:55px;font-family:'Noto Serif',serif;font-size:17px;color:var(--white)}
.mainnav li.active{position:relative}
.mainnav li.active::after{content:"";position:absolute;left:50%;bottom:-17px;margin-left:-5px;border:5px solid transparent;border-bottom-color:var(--green)}
.brand{position:absolute;left:122px;top:0;width:164px;height:175px;background:var(--white);border-radius:0 0 30px 30px;z-index:3;display:flex;flex-direction:column;align-items:center;justify-content:center;gap:8px;box-shadow:0 1px 3px rgba(0,0,0,.15)}
.brand .mark{width:44px;height:44px;border-radius:50%;background:var(--green)}
.brand .name{font-family:'Noto Serif',serif;font-size:17px;line-height:1.2;text-align:center;color:var(--ink)}
.hero{position:absolute;left:0;top:139px;width:1200px;height:483px;background:linear-gradient(100deg,#2a2624 0%,#3b332c 30%,#8a7565 52%,#4a3f38 70%,#2b2623 100%)}
.hero h1{position:absolute;left:113px;top:326px;font-family:'Noto Serif',serif;font-style:italic;font-weight:400;font-size:40px;line-height:42px;color:var(--white)}
.dots{position:absolute;left:115px;top:433px;display:flex;gap:8px}
.dots i{width:12px;height:12px;border-radius:50%;background:var(--dot)}
.dots i.on{background:var(--green)}
.about{position:absolute;left:121px;top:654px;width:620px}
h2{font-family:'Noto Serif',serif;font-weight:400;font-size:26px;color:var(--ink);letter-spacing:.3px}
.about p{margin-top:18px;font-size:15px;line-height:26.2px;color:var(--text)}
.video{position:absolute;left:774px;top:654px}
.player{position:absolute;left:-4px;top:42px;width:313px;height:174px;background:var(--white);box-shadow:0 1px 4px rgba(0,0,0,.3);padding:7px}
.frame{width:299px;height:160px;background:linear-gradient(90deg,#3a3a3c 0%,#7a7a78 40%,#d9d4cc 70%,#b8a28a 100%);position:relative}
.play{position:absolute;left:121px;top:51px;width:62px;height:40px;background:#111}
.play svg{display:block;margin:11px auto}
.controls{position:absolute;left:0;bottom:0;width:100%;height:15px;background:#1c1c1c}
.controls::before{content:"";position:absolute;left:0;top:0;width:56px;height:3px;background:#c00}
.social{position:absolute;left:0;top:910px;width:1200px;height:69px;background:var(--band)}
.social .circles{position:absolute;left:126px;top:16px;display:flex;gap:21px}
.social .circles span{width:40px;height:40px;border-radius:50%;background:var(--white)}
.signup{position:absolute;left:550px;top:17px;display:flex;gap:11px}
.signup .field{width:345px;height:36px;background:var(--white);border:1px solid #ccc;font-family:'Roboto Condensed',sans-serif;font-size:14px;color:#777;padding:9px 14px}
.signup .btn{width:172px;height:36px;background:var(--lime);color:var(--white);font-family:'Oswald',sans-serif;font-size:19px;text-align:center;line-height:36px}
.footer{position:absolute;left:0;top:979px;width:1200px;height:95px;background:var(--foot)}
.footer ul{list-style:none;position:absolute;left:124px;top:23px;display:flex;gap:19px;font-size:13px;color:var(--white)}
.footer p{position:absolute;left:124px;top:53px;font-size:14px;color:#b8b8b8;letter-spacing:.3px}
.footer .squares{position:absolute;left:894px;top:31px;display:flex;gap:6px}
.footer .squares span{width:40px;height:35px;background:#666}
.footer .squares span.first{background:#3b5a9a}
</style>
</head>
<body>
<header class="topbar">
  <div class="follow">Follow Us On <span class="icon" aria-label="social link"></span><span class="icon" aria-label="social link"></span><span class="icon" aria-label="social link"></span></div>
  <nav class="utility"><span>Getting Started</span><span class="sep">|</span><span>Who We Are</span><span class="sep">|</span><span>Contact Us</span></nav>
</header>
<div class="brand"><span class="mark"></span><span class="name">Bramblewood Joinery</span></div>
<nav class="mainnav">
  <ul><li class="active">Home</li><li>Customer Experience</li><li>Professional</li><li>Portfolio</li><li>Cabinet Hardware</li></ul>
</nav>
<section class="hero" role="img" aria-label="Photo of a modern dark kitchen with an island and large windows at sunset">
  <h1>Welcome to Bramblewood<br>Joinery &amp; Fixtures</h1>
  <div class="dots"><i></i><i class="on"></i><i></i><i></i></div>
</section>
<section class="about">
  <h2>WHO WE ARE</h2>
  <p>Established in 1966, Bramblewood Joinery has long stood as one of the Midwest's most renowned makers of custom cabinets and fixtures. Our handcrafted, award-winning creations have been chosen by hundreds of noteworthy homebuilders. And while we custom build cabinets, we built our business around the belief that our customers absolutely, unequivocally come first. From day one, our mission has been to help turn the houses that people live in to the homes they've always dreamed of.</p>
</section>
<section class="video">
  <h2>WATCH OUR VIDEO</h2>
  <div class="player">
    <div class="frame" role="img" aria-label="Video still of a white cabinet kitchen with a built-in oven">
      <div class="play"><svg width="16" height="18" viewBox="0 0 16 18"><path d="M0 0L16 9L0 18Z" fill="#fff"/></svg></div>
      <div class="controls"></div>
    </div>
  </div>
</section>
<section class="social">
  <div class="circles"><span aria-label="social link"></span><span aria-label="social link"></span><span aria-label="social link"></span><span aria-label="social link"></span></div>
  <div class="signup"><div class="field">Enter your email id and get updates!</div><div class="btn">SUBSCRIBE</div></div>
</section>
<footer class="footer">
  <ul><li>ADVICE</li><li>|</li><li>ABOUT</li><li>|</li><li>CONTACT</li><li>|</li><li>PRIVACY POLICY</li><li>|</li><li>TERMS &amp; CONDITION</li></ul>
  <p>copyright© 2014 Bramblewood. All Rights Reserved.</p>
  <div class="squares"><span class="first" aria-label="social link"></span><span aria-label="social link"></span><span aria-label="social link"></span><span aria-label="social link"></span></div>
</footer>
</body>
</html>
```